Dorwin's Coating & Renewal Letterhead Design We want to revamp out old traditional letterhead with the new logo designs that are attached. We are working on getting all our company items from vehicles, business, cards, t-shirts, letterhead to match. This should include company colors, fonts, and flow of items that we have attached below.

Industry/Entity Type

Construction Company

Font styles to use
Sans Serif
Other font styles liked:
• Bold with outline

Colors
ec1f27
ffffff

Requirements
Must have
• Company Name: Dorwin's Coating & Renewal
• Address: 4728 SW 81st Ter Halverd cove fl 39417
• Office Number: (555) 413-2986
• Email: Dorwinrenewal@mailbrook.example
• License Number: KRT8046392
Nice to have
• Company Colors: red, white, black, and grey

```html
<!DOCTYPE html>
<html lang="en">
<head>
<meta charset="utf-8">
<title>Dorwin's Coating &amp; Renewal — Letterhead</title>
<link href="https://fonts.googleapis.com/css2?family=Arimo:wght@400;700&display=swap" rel="stylesheet">
<style>
  :root {
    --brand-red: #ec1f27;
    --ink-black: #161616;
    --text-grey: #7a7a7a;
    --rule-grey: #d4d4d4;
    --paper: #ffffff;
    --backdrop: #dfe2e4;
  }
  * { box-sizing: border-box; margin: 0; padding: 0; }
  html, body {
    width: 1200px; height: 784px; overflow: hidden;
    background: var(--backdrop);
    font-family: "Arimo", Arial, sans-serif;
  }
  .letterhead {
    position: absolute; left: 338px; top: 22px;
    width: 524px; height: 740px;
    background: var(--paper);
    box-shadow: 0 6px 18px rgba(0,0,0,.12);
    overflow: hidden;
  }
  .corner { position: absolute; }
  .corner--top { top: 0; right: 0; }
  .corner--bottom { bottom: 0; left: 0; }

  .brand {
    position: absolute; top: 42px; right: 44px;
    text-align: right; color: var(--brand-red);
    font-weight: 700; line-height: 1;
  }
  .brand__name { font-size: 34px; letter-spacing: 1px; display: block; }
  .brand__line { font-size: 11.5px; letter-spacing: 2.6px; display: block; margin-top: 5px; }

  .contact {
    position: absolute; top: 150px; right: 30px; width: 150px;
    padding-left: 12px; border-left: 1px solid var(--rule-grey);
    font-size: 7.6px; color: var(--text-grey); line-height: 1.55;
  }
  .contact__row { display: flex; gap: 5px; align-items: flex-start; }
  .contact__row--address { color: var(--brand-red); font-weight: 700; margin-bottom: 3px; }
  .contact__icon { flex: 0 0 9px; width: 9px; height: 9px; margin-top: 1px; }

  .body-copy {
    position: absolute; top: 150px; left: 58px; width: 300px;
    font-size: 8.2px; line-height: 1.6; color: var(--text-grey);
  }
  .body-copy p { text-indent: 14px; margin-bottom: 12px; }
</style>
</head>
<body>
  <main class="letterhead">
    <svg class="corner corner--top" width="150" height="150" viewBox="0 0 150 150" aria-hidden="true">
      <defs>
        <linearGradient id="blackCorner" x1="0" y1="0" x2="1" y2="1">
          <stop offset="0" stop-color="#555"/>
          <stop offset="1" stop-color="#000"/>
        </linearGradient>
      </defs>
      <polygon points="62,0 150,0 150,150" fill="url(#blackCorner)"/>
    </svg>
    <svg class="corner corner--bottom" width="110" height="190" viewBox="0 0 110 190" aria-hidden="true">
      <polygon points="0,0 110,190 0,190" fill="var(--brand-red)"/>
    </svg>

    <header class="brand">
      <span class="brand__name">DORWIN'S</span>
      <span class="brand__line">COATING &amp; RENEWAL</span>
    </header>

    <address class="contact">
      <div class="contact__row contact__row--address">
        <svg class="contact__icon" viewBox="0 0 10 10" aria-hidden="true"><circle cx="5" cy="5" r="5" fill="var(--brand-red)"/><path d="M5 2.2a1.8 1.8 0 0 1 1.8 1.8C6.8 5.4 5 7.6 5 7.6S3.2 5.4 3.2 4A1.8 1.8 0 0 1 5 2.2z" fill="#fff"/></svg>
        <span>4728 SW 81st Ter<br>Halverd cove fl 39417</span>
      </div>
      <div class="contact__row">
        <svg class="contact__icon" viewBox="0 0 10 10" aria-hidden="true"><circle cx="5" cy="5" r="5" fill="var(--brand-red)"/><path d="M3.3 2.6l1 1-.5.7a3.5 3.5 0 0 0 1.9 1.9l.7-.5 1 1-.6.8C5 7.3 2.7 5 2.5 3.2z" fill="#fff"/></svg>
        <span>(555) 413-2986</span>
      </div>
      <div class="contact__row">
        <svg class="contact__icon" viewBox="0 0 10 10" aria-hidden="true"><circle cx="5" cy="5" r="5" fill="var(--brand-red)"/><rect x="3" y="3" width="4" height="4" fill="#fff"/></svg>
        <span>License: KRT8046392</span>
      </div>
      <div class="contact__row">
        <svg class="contact__icon" viewBox="0 0 10 10" aria-hidden="true"><circle cx="5" cy="5" r="5" fill="var(--brand-red)"/><rect x="2.6" y="3.3" width="4.8" height="3.4" fill="#fff"/><path d="M2.6 3.3L5 5.2 7.4 3.3" fill="none" stroke="var(--brand-red)" stroke-width=".6"/></svg>
        <span>Dorwinrenewal@mailbrook.example</span>
      </div>
      <div class="contact__row">
        <svg class="contact__icon" viewBox="0 0 10 10" aria-hidden="true"><circle cx="5" cy="5" r="5" fill="var(--brand-red)"/><circle cx="5" cy="5" r="2.3" fill="none" stroke="#fff" stroke-width=".7"/></svg>
        <span>www.dorwinrenewal.example</span>
      </div>
    </address>

    <section class="body-copy">
      <p>Lorem Ipsum is simply dummy text of the printing and typesetting industry. Lorem Ipsum has been the industry's standard dummy text ever since the 1500s, when an unknown printer took a galley of type and scrambled it to make a type specimen book. It has survived not only five centuries, but also the leap into electronic typesetting, remaining essentially unchanged. It was popularised in the 1960s with the release of Typeline sheets containing Lorem Ipsum passages, and more recently with desktop publishing software like Quillset Layout including versions of Lorem Ipsum.</p>
      <p>It is a long established fact that a reader will be distracted by the readable content of a page when looking at its layout. The point of using Lorem Ipsum is that it has a more-or-less normal distribution of letters, as opposed to using 'Content here, content here', making it look like readable English. Many desktop publishing packages and web page editors now use Lorem Ipsum as their default model text, and a search for 'lorem ipsum' will uncover many web sites still in their infancy. Various versions have evolved over the years, sometimes by accident, sometimes on purpose (injected humour and the like).</p>
      <p>Contrary to popular belief, Lorem Ipsum is not simply random text. It has roots in a piece of classical Latin literature from 45 BC, making it over 2000 years old. Harold Venmire, a Latin professor at Larkfield College in Virginia, looked up one of the more obscure Latin words, consectetur, from a Lorem Ipsum passage, and going through the cites of the word in classical literature, discovered the undoubtable source. Lorem Ipsum comes from sections 1.10.32 and 1.10.33 of "de Finibus Bonorum et Malorum" structures, to generate Lorem Ipsum which looks reasonable. The generated Lorem Ipsum is therefore always free from repetition, injected humour, or non-characteristic words etc.</p>
    </section>
  </main>
</body>
</html>
```